Unusual Options Activity Graphic Card Design for Finance App

We are developing a financial data platform called Vantix Pulse, and we need a visually striking, mobile-optimized graphic card design to display unusual options activity. The card will be featured in our mobile app and marketing materials, inspired by platforms like Quorafin and Marlow Tide.
🔹 Design Goals:
Modern, clean, and professional aesthetic
Use vibrant electric blue, green, or dark theme gradients
Must feel tech-savvy and finance-oriented
Layout should be optimized for vertical mobile format (portrait)
🔹 Information to Include in the Card:
Ticker Symbol (e.g., QRV) with colored badge
Date & Time of trade
Trade Type (e.g., Sweep Call / Put)
Execution Type (At Ask or At Bid)
Strike Price
Expiration Date
Premium (e.g., $342.75K)
Size@Price (e.g., 6995@$0.49)
Volume
Open Interest
Branding at bottom: “Vantix Pulse” in modern font
🔹 Inspiration:
Quorafin’s profit/loss cards
Clean fintech dashboards (Sparvane, Marlow Tide, Kestrowe Console)
Please provide the final deliverable in high-resolution PNG and layered PSD or Figma file for future edits.
Stock Market Traders
Finance

```html
<!DOCTYPE html>
<html lang="en">
<head>
<meta charset="UTF-8">
<title>Vantix Pulse – Options Activity Cards</title>
<link rel="stylesheet" href="https://fonts.googleapis.com/css2?family=Poppins:wght@400;500;600;700&display=swap">
<style>
  :root {
    --stage-deep: #04123f;
    --stage-mid: #0a3478;
    --card-top: #0b4f55;
    --card-mid: #14835a;
    --card-bottom: #0c4590;
    --bar-start: #0a7a66;
    --bar-end: #14b586;
    --bar-edge: #37d6a0;
    --badge-fill: #0a3d4c;
    --accent-teal: #2fe0c0;
    --label-teal: #3fe3cf;
    --text-white: #ffffff;
    --panel-fill: rgba(10, 50, 100, 0.45);
    --art-green-a: #b6ff4a;
    --art-green-b: #1fb83c;
    --art-blue-a: #3fe0a0;
    --art-blue-b: #1372b8;
  }
  * { margin: 0; padding: 0; box-sizing: border-box; }
  html, body { width: 1200px; height: 675px; overflow: hidden; }
  body {
    font-family: "Poppins", sans-serif;
    background: radial-gradient(ellipse at 50% 30%, var(--stage-mid) 0%, var(--stage-deep) 100%);
    position: relative;
  }
  .option-card {
    position: absolute;
    top: 68px;
    width: 340px;
    height: 538px;
    overflow: hidden;
    background:
      radial-gradient(circle at 58% 45%, rgba(120, 230, 90, 0.55) 0%, rgba(40, 170, 90, 0.25) 30%, transparent 60%),
      linear-gradient(180deg, var(--card-top) 0%, var(--card-mid) 48%, #0f6a78 72%, var(--card-bottom) 100%);
    box-shadow: 0 12px 40px rgba(0, 0, 0, 0.45);
  }
  .option-card--green { left: 203px; }
  .option-card--blue { left: 657px; }

  .header-bar {
    position: absolute;
    left: 32px; top: 30px;
    width: 275px; height: 35px;
    border-radius: 5px;
    border: 1px solid var(--bar-edge);
    background: linear-gradient(90deg, var(--bar-start), var(--bar-end));
    display: flex; align-items: center;
    padding: 0 12px 0 5px;
  }
  .ticker-badge {
    background: var(--badge-fill);
    color: var(--text-white);
    font-weight: 600;
    font-size: 17px;
    line-height: 1;
    padding: 5px 10px 4px;
    border-radius: 4px;
    border: 1px solid rgba(255,255,255,0.25);
  }
  .trade-stamp {
    margin-left: auto;
    color: var(--text-white);
    font-size: 13.5px;
    font-weight: 500;
    letter-spacing: 0.3px;
    word-spacing: 8px;
  }
  .trade-type {
    position: absolute;
    left: 34px; top: 78px;
    color: var(--text-white);
    font-size: 23.5px;
    font-weight: 500;
    line-height: 1;
  }
  .execution-type {
    position: absolute;
    left: 35px; top: 106px;
    color: var(--accent-teal);
    font-size: 15.5px;
    font-weight: 500;
    line-height: 1;
  }
  .hero-art {
    position: absolute;
    left: 50px; top: 125px;
    width: 250px; height: 275px;
    border-radius: 50%;
    filter: blur(2px);
  }
  .option-card--green .hero-art {
    background: radial-gradient(ellipse at 55% 45%, var(--art-green-a) 0%, var(--art-green-b) 45%, transparent 72%);
  }
  .option-card--blue .hero-art {
    background: radial-gradient(ellipse at 55% 45%, var(--art-blue-a) 0%, var(--art-blue-b) 45%, transparent 72%);
  }
  .stats-panel {
    position: absolute;
    left: 13px; top: 419px;
    width: 314px; height: 70px;
    border-radius: 8px;
    background: var(--panel-fill);
    display: grid;
    grid-template-columns: 69px 82px 60px 1fr;
    grid-auto-rows: 15px;
    row-gap: 0;
    align-content: center;
    padding: 0 21px;
    font-size: 10px;
    line-height: 15px;
  }
  .stat-label { color: var(--label-teal); }
  .stat-value { color: var(--text-white); }
  .stat-value--end { text-align: right; }
  .brand-mark {
    position: absolute;
    left: 0; right: 0; top: 500px;
    text-align: center;
    color: var(--text-white);
    font-weight: 700;
    font-size: 15px;
    letter-spacing: 1.5px;
  }
</style>
</head>
<body>

  <article class="option-card option-card--green">
    <div class="header-bar">
      <span class="ticker-badge">QRV</span>
      <span class="trade-stamp">04/19/2025 10:30</span>
    </div>
    <h1 class="trade-type">SWEEP CALL</h1>
    <p class="execution-type">AT ASK</p>
    <div class="hero-art" role="img" aria-label="3D green upward arrow surrounded by floating question marks"></div>
    <div class="stats-panel">
      <span class="stat-label">Strike Price</span><span class="stat-value">$10</span>
      <span class="stat-label">Expiration</span><span class="stat-value stat-value--end">Apr 28 2025</span>
      <span class="stat-label">Premium</span><span class="stat-value">$342.75K</span>
      <span class="stat-label">Volume</span><span class="stat-value stat-value--end">0000</span>
      <span class="stat-label">Size@Price</span><span class="stat-value">6995@0.49</span>
      <span class="stat-label">Open Interest</span><span class="stat-value stat-value--end">0000</span>
    </div>
    <p class="brand-mark">VANTIX PULSE</p>
  </article>

  <article class="option-card option-card--blue">
    <div class="header-bar">
      <span class="ticker-badge">QRV</span>
      <span class="trade-stamp">04/19/2025 10:30</span>
    </div>
    <h1 class="trade-type">SWEEP CALL</h1>
    <p class="execution-type">AT ASK</p>
    <div class="hero-art" role="img" aria-label="3D teal-blue upward arrow surrounded by floating question marks"></div>
    <div class="stats-panel">
      <span class="stat-label">Strike Price</span><span class="stat-value">$10</span>
      <span class="stat-label">Expiration</span><span class="stat-value stat-value--end">Apr 28 2025</span>
      <span class="stat-label">Premium</span><span class="stat-value">$342.75K</span>
      <span class="stat-label">Volume</span><span class="stat-value stat-value--end">0000</span>
      <span class="stat-label">Size@Price</span><span class="stat-value">6995@0.49</span>
      <span class="stat-label">Open Interest</span><span class="stat-value stat-value--end">0000</span>
    </div>
    <p class="brand-mark">VANTIX PULSE</p>
  </article>

</body>
</html>
```